Lifecoach needs website design based on a standard Wordpress theme

I need a website for my new lifecoaching business that can be easily implemented in Wordpress, it needs to be compatible with a standard Wordpress theme. So I can place the pictures, texts etc. in a standard theme of Wordpress.

I want the design to be a very good feeling and playfull one, based on my logo.

Target Market(s)

I will coach people to reach their goals and dreams in life.

Industry/Entity Type

Business

Requirements
Must have
• Can be easy implemented in Wordpress.
Nice to have
• Photo's of nature are nice.

```html
<!DOCTYPE html>
<html lang="en">
<head>
<meta charset="utf-8">
<title>Mara ten Brink Lifecoach</title>
<link href="https://fonts.googleapis.com/css2?family=Open+Sans:ital,wght@0,400;0,600;0,700;1,400&display=swap" rel="stylesheet">
<style>
:root{
  --navy:#0c5a8c;
  --navy-deep:#0d4d7f;
  --sky:#1ab2ea;
  --ink:#555;
  --text:#666;
  --title:#1c5b8c;
  --red:#e0493b;
  --salmon:#ec8f82;
  --footer:#9eabb3;
  --white:#fff;
}
*{box-sizing:border-box;margin:0;padding:0}
html,body{width:823px;height:1200px;overflow:hidden;background:var(--white)}
body{position:relative;font-family:"Open Sans",Arial,sans-serif;color:var(--text)}
.abs{position:absolute}

/* header */
.brand-mark{left:70px;top:8px;width:52px;height:52px;border-radius:50%;background:var(--navy)}
.brand-name{left:128px;top:18px;color:var(--navy);font-weight:600;font-size:16px;letter-spacing:.8px;line-height:18px}
.brand-name span{display:block;font-size:10.5px;letter-spacing:1.5px;padding-left:38px}
.btn-sign{left:664px;top:16px;width:43px;height:17px;background:#a6a6a6;color:#fff;font-size:8px;font-weight:600;text-align:center;line-height:17px}
.btn-login{left:712px;top:16px;width:43px;height:17px;background:var(--sky);color:#fff;font-size:8px;font-weight:600;text-align:center;line-height:17px}
.search{left:610px;top:38px;width:124px;height:18px;background:#e6e6e6}
.search-btn{left:734px;top:38px;width:21px;height:18px;background:var(--navy)}

/* nav */
.nav{left:0;top:69px;width:823px;height:31px;background:var(--navy)}
.nav a{position:absolute;top:0;height:31px;line-height:31px;color:#fff;font-size:10.4px;text-decoration:none}
.nav a.active{background:var(--sky);width:63px;text-align:center}

/* hero */
.hero{left:0;top:100px;width:823px;height:355px;background:linear-gradient(180deg,#c79a2a 0%,#6f8a2a 25%,#4d7a2c 55%,#9d8a34 80%,#d9a43c 100%)}
.hero-arrow{width:25px;height:25px;border:2px solid rgba(255,255,255,.85);border-radius:50%;top:255px}
.hero-card{left:559px;top:188px;width:196px;height:178px;background:rgba(30,50,35,.55);text-align:center;color:#fff}
.hero-card h1{font-weight:400;font-size:20px;margin-top:17px;letter-spacing:.5px}
.hero-card h2{font-weight:400;font-size:14px;margin-top:1px}
.hero-card p{font-size:9.6px;line-height:14px;padding:0 20px;margin-top:11px}
.hero-card .join{display:inline-block;margin-top:11px;background:var(--sky);padding:0 13px;height:22px;line-height:22px;font-size:9.6px}

/* about */
.section-title{left:0;width:823px;text-align:center;font-size:17px;color:var(--ink)}
.photo{background:#bbb}
.about-copy{font-size:8.8px;line-height:15px;text-align:justify;color:#777;hyphens:auto;-webkit-hyphens:auto}
.caption{font-size:11.5px;line-height:15px;text-align:center;color:#777}

/* blog */
.blog-title em{font-style:italic;color:#777}
.blog-title b{font-weight:400;color:#444;letter-spacing:.5px}
.date{left:71px;top:711px;width:98px;height:15px;background:var(--sky);color:#fff;font-size:7.5px;line-height:15px;text-align:center}
.tag{left:313px;top:713px;color:var(--red);font-size:7.5px;font-style:italic;font-weight:600}
.post-title{left:70px;top:738px;font-size:12px;font-weight:600;color:var(--title)}
.post-text{left:70px;top:908px;width:326px;font-size:8.8px;line-height:14px;color:#666}
.item-text{left:497px;width:260px;font-size:8.8px;line-height:14px;color:#666}
.item-text time{display:block;color:var(--salmon)}
.read-more{left:372px;top:959px;color:var(--red);font-size:10.4px}

/* footer */
.footer{left:0;top:1013px;width:823px;height:156px;background:var(--footer);border-top:2px solid var(--sky)}
.foot-name{left:70px;top:1034px;color:#fff;font-size:15px;letter-spacing:.5px}
.foot-copy{left:70px;top:1075px;width:162px;color:#fff;font-size:8px;line-height:11px;text-align:justify}
.foot-head{color:#fff;font-size:9.6px;font-weight:600}
.subscribe-box{left:276px;top:1079px;width:164px;height:28px;border:2px solid #fff}
.subscribe-note{left:275px;top:1115px;width:163px;color:#fff;font-size:7.4px;font-weight:700;line-height:11px;text-align:justify}
.foot-link{color:#fff;font-size:7.6px}
.social{left:709px;width:21px;height:21px;border-radius:2px}
.bottom{left:0;top:1169px;width:823px;height:31px;background:var(--navy-deep);color:#fff;font-size:8.8px;text-align:center;line-height:31px}
</style>
</head>
<body>

<header>
  <div class="abs brand-mark" aria-hidden="true"></div>
  <div class="abs brand-name">MARA TEN BRINK<span>LIFECOACH</span></div>
  <div class="abs btn-sign">SIGNUP</div>
  <div class="abs btn-login">LOGIN</div>
  <div class="abs search"></div>
  <div class="abs search-btn">
    <svg width="21" height="18" viewBox="0 0 21 18"><circle cx="10" cy="8.5" r="3" fill="none" stroke="#fff" stroke-width="1.3"/><line x1="12.2" y1="10.7" x2="14" y2="12.5" stroke="#fff" stroke-width="1.4"/></svg>
  </div>
</header>

<nav class="abs nav">
  <a class="active" style="left:70px">Home</a>
  <a style="left:150px">Coaching Programs</a>
  <a style="left:273px">Blog</a>
  <a style="left:327px">Tools &amp; Support</a>
  <a style="left:434px">Success Stories</a>
  <a style="left:537px">About Us</a>
  <a style="left:613px">Contact Us</a>
  <a style="left:694px">Join Now</a>
</nav>

<section>
  <div class="abs hero" role="img" aria-label="Sunlit tree in a golden meadow"></div>
  <div class="abs hero-arrow" style="left:26px">
    <svg width="21" height="21" viewBox="0 0 21 21"><polyline points="12,6 8,10.5 12,15" fill="none" stroke="#fff" stroke-width="1.5"/></svg>
  </div>
  <div class="abs hero-arrow" style="left:773px">
    <svg width="21" height="21" viewBox="0 0 21 21"><polyline points="9,6 13,10.5 9,15" fill="none" stroke="#fff" stroke-width="1.5"/></svg>
  </div>
  <div class="abs hero-card">
    <h1>MARA TEN BRINK</h1>
    <h2>LIFECOACH</h2>
    <p>We specialize in transition life coaching for personal and professional empowerment.</p>
    <span class="join">Join Now</span>
  </div>
</section>

<section>
  <h2 class="abs section-title" style="top:464px;font-weight:600">About Us</h2>
  <div class="abs photo" style="left:70px;top:499px;width:116px;height:103px;background:linear-gradient(180deg,#e9eef2,#a9b8c6)" role="img" aria-label="Smiling business team"></div>
  <p class="abs about-copy" style="left:203px;top:496px;width:210px">long established fact that a reader will be distracted by the readable content of a page when looking at its layout. The point of using Lorem Ipsum is that it has a more-or-less normal distribution of letters, as opposed to using 'Content here, content here', making it look like readable English. Many desktop publishing packages</p>
  <p class="abs about-copy" style="left:70px;top:612px;width:343px">The point of using Lorem Ipsum is that it has a more-or-less normal distribution of letters, as opposed to using 'Content here, content here', making it look like readable English. Many desktop publishing packages</p>
  <div class="abs photo" style="left:443px;top:499px;width:147px;height:102px;background:linear-gradient(180deg,#7fa6cf 0%,#e8d9a6 45%,#6da53a 70%,#4a8b25 100%)" role="img" aria-label="Man raising arms on a green field at sunrise"></div>
  <div class="abs photo" style="left:608px;top:499px;width:147px;height:102px;background:linear-gradient(180deg,#8a6a4e,#3a3a3e)" role="img" aria-label="Group of business professionals"></div>
  <p class="abs caption" style="left:443px;top:613px;width:147px">Transition life coaching for personal</p>
  <p class="abs caption" style="left:602px;top:613px;width:159px">Transition life coaching for professional empowerment</p>
</section>

<section>
  <h2 class="abs section-title blog-title" style="top:675px;font-weight:400"><em>from the</em> <b>BLOG</b></h2>
  <div class="abs date">23 September 2013</div>
  <svg class="abs" style="left:298px;top:713px" width="11" height="10" viewBox="0 0 11 10"><path d="M0 1 L4 1 L9 5.5 L5.5 9 L0 4 Z" fill="var(--navy)"/><circle cx="2" cy="3" r="0.9" fill="#fff"/></svg>
  <div class="abs tag">Fashion</div>
  <h3 class="abs post-title">Duis dapibus aliquam mi, eget euismod sem scelerisque ut.</h3>
  <div class="abs photo" style="left:70px;top:761px;width:322px;height:141px;background:linear-gradient(180deg,#dfe8ee 0%,#b7cfae 50%,#c9b39a 75%,#9fb27a 100%)" role="img" aria-label="Hands holding a small tree"></div>
  <p class="abs post-text">Nunc nec massa et risus iaculis interdum et sed mi. Nam viverra ac neque eu liquet. Maecenas posuere, neque non vestibulum sodales, arcu diam nterdum nulla, in molestie magna magna vitae</p>

  <div class="abs photo" style="left:435px;top:762px;width:49px;height:50px;background:linear-gradient(180deg,#e8e8e8,#4a4a52)" role="img" aria-label="Business meeting"></div>
  <div class="abs photo" style="left:435px;top:826px;width:49px;height:49px;background:linear-gradient(135deg,#7fb4e2,#1e5d9c)" role="img" aria-label="Globe on a keyboard"></div>
  <div class="abs photo" style="left:435px;top:888px;width:49px;height:49px;background:linear-gradient(180deg,#f2f2f2,#8fbf4a 60%,#d63a2a)" role="img" aria-label="Colourful growth chart with figures"></div>

  <p class="abs item-text" style="top:761px">Lorem ipsum dolor sit amet, consectetur adipiscing elit.Morbi blandit velit id dolor fermentum, non<br>posuere libero posuere.<time>26 Aug, 2013</time></p>
  <p class="abs item-text" style="top:824px">Lorem ipsum dolor sit amet, consectetur adipiscing elit.Morbi blandit velit id dolor fermentum, non<br>posuere libero posuere.<time>26 Aug, 2013</time></p>
  <p class="abs item-text" style="top:886px">Lorem ipsum dolor sit amet, consectetur adipiscing elit.Morbi blandit velit id dolor fermentum, non<br>posuere libero posuere.<time>26 Aug, 2013</time></p>

  <div class="abs read-more">Read more...</div>
  <svg class="abs" style="left:442px;top:962px" width="10" height="10" viewBox="0 0 10 10"><path d="M1 4 H6 V1.5 L9.5 5 L6 8.5 V6 H1 Z" fill="var(--red)"/></svg>
</section>

<footer>
  <div class="abs footer"></div>
  <div class="abs foot-name">MARA TEN BRINK</div>
  <p class="abs foot-copy">eusmod tempor incididunt ut labore et dolore magna aliqua. Ut enim ad minim veniam, quis nostrud exercitation ullamco laboris nisi ut aliquip ex ea commodo consequat.</p>

  <div class="abs foot-head" style="left:276px;top:1040px">Subscribe</div>
  <div class="abs subscribe-box">
    <svg class="abs" style="left:140px;top:7px" width="14" height="10" viewBox="0 0 14 10"><path d="M1 5 H12 M8 1 L12 5 L8 9" fill="none" stroke="#fff" stroke-width="1"/></svg>
  </div>
  <p class="abs subscribe-note">eusmod tempor incididunt ut labore et dolore magna aliqua.</p>

  <div class="abs foot-head" style="left:492px;top:1040px">Explore</div>
  <div class="abs foot-link" style="left:492px;top:1076px">ipsum dolor</div>
  <div class="abs foot-link" style="left:492px;top:1096px">curve</div>
  <div class="abs foot-link" style="left:492px;top:1115px">roeus</div>
  <div class="abs foot-link" style="left:492px;top:1134px">Freshloop</div>
  <div class="abs foot-link" style="left:582px;top:1076px">Lorem ipsum</div>
  <div class="abs foot-link" style="left:582px;top:1096px">Northwind</div>
  <div class="abs foot-link" style="left:582px;top:1115px">Searchly</div>
  <div class="abs foot-link" style="left:582px;top:1134px">Mailbay</div>

  <div class="abs foot-head" style="left:679px;top:1043px">Staying in touch</div>
  <div class="abs social" style="top:1075px;background:#3b5c9a" aria-label="Social profile"></div>
  <div class="abs social" style="top:1103px;background:#c4ccd1" aria-label="Social profile"></div>
  <div class="abs social" style="top:1130px;background:#c4ccd1" aria-label="Social profile"></div>

  <div class="abs bottom">© 2014 Corvane. All Rights Reserved.</div>
</footer>

</body>
</html>
```